Home Page Design (+50 More Pages To Winning Designer!)

We have a 50+ page website, but we're starting with the home page. The winning designer will get all 50+ pages to design as a 2nd project, so make sure you do your best!

Velorane is in the private jet industry and needs a re-designed website.

We have created the structure for the website and content inside of Frandle.io (THESE ARE ONLY ROUGH A.I. GENERATED WIREFRAMES AND DO NOT NEED TO BE FOLLOWED EXACTLY) - https://www.frandle.io/app/project/K482915_qWmRtZaLs-KDnHoUvvy82QJ5cfhaR61trkwqlDV3Hm

Take the content from the 'Home Page' under the 'Wireframe' tab on the Frandle.io link above, but feel free to re-design the page in a better way as these are only A.I. generated wireframes.

We want a DARK theme.... High quality, luxurious feel, greyscale colors. Attached is a brand guideline (BUT THIS IS NOT A 100% BRAND GUIDELINE, YOU CAN CHANGE COLORS AND FONTS AND MAKE CHANGES IF YOU HAVE BETTER IDEAS) and attached is our logo. We are also attaching some examples of other apps and websites to give you a guideline of what we're looking for for this design project.

The final design MUST communicate luxury using high-quality imagery of large cabin luxurious private jets.
Updates

ENTRIES THAT DO NOT FOLLOW THE PROJECT BRIEF WILL BE AUTOMATICALLY DISCARDED. FOLLOW THE INSTRUCTIONS!

Industry/Entity Type

Travel

Number of Pages Required

1 page

Font styles to use
Sans Serif

Colors

Designer to choose colors to be used in the design.

Requirements
Must have
• Follow wireframe and use content in wireframe (see Frandle.io link)

```html
<!DOCTYPE html>
<html lang="en">
<head>
<meta charset="utf-8">
<title>Velorane — Private Jet Programs</title>
<link href="https://fonts.googleapis.com/css2?family=Inter:wght@300;400;500;600;700&display=swap" rel="stylesheet">
<style>
:root{
  --ink:#1f1f1f;
  --dark:#333333;
  --darker:#2b2b2b;
  --footer:#454545;
  --mid:#7c7c7c;
  --muted:#8d8d8d;
  --light:#f2f2f2;
  --white:#ffffff;
  --line:#9a9a9a;
  --star:#f5b301;
}
*{box-sizing:border-box;margin:0;padding:0}
html,body{width:1200px;height:4658px;overflow:hidden}
body{font-family:'Inter',sans-serif;color:var(--ink);background:var(--white);position:relative}
section,header,footer{position:absolute;left:0;width:1200px}
.abs{position:absolute}
.center{left:0;width:1200px;text-align:center}

/* hero */
.hero{top:0;height:555px;overflow:hidden}
.hero-photo{position:absolute;inset:0;background:linear-gradient(180deg,#4e4e4e 0%,#666 45%,#7a7a7a 75%,#6c6c6c 100%)}
.brand{font-weight:300;color:var(--white);letter-spacing:-0.5px}
.brand-sm{left:132px;top:26px;font-size:30px}
.nav{right:130px;top:30px;display:flex;gap:38px}
.nav a{color:var(--white);text-decoration:none;font-size:18px;font-weight:500}
.hero-title{top:172px;font-size:72px;font-weight:700;color:var(--white);letter-spacing:-0.5px}
.hero-sub{top:266px;font-size:24px;color:var(--white)}
.hero-actions{top:336px;display:flex;justify-content:center;gap:20px}
.btn{display:inline-flex;align-items:center;justify-content:center;font-size:16px;font-weight:500;color:var(--white);text-decoration:none}
.btn-solid{background:var(--dark);width:137px;height:44px}
.btn-outline{border:2px solid #d0d0d0;width:137px;height:44px}

/* intro */
.intro{top:555px;height:470px;background:var(--dark);overflow:hidden;color:var(--white)}
.intro p{left:132px;top:76px;width:840px;font-size:22px;line-height:32px}
.checks{left:132px;top:246px;list-style:none}
.checks li{display:flex;align-items:center;gap:14px;font-size:17px;height:40.5px}
.watermark{left:575px;top:320px;font-size:142px;font-weight:300;color:#4b4b4b;letter-spacing:-2px;white-space:nowrap}

/* benefits */
.benefits{top:1025px;height:506px;background:var(--white)}
.sec-title{font-size:31px;font-weight:700}
.benefits .sec-title{top:52px}
.grey{color:var(--muted)}
.sec-sub{font-size:15px}
.benefits .sec-sub{top:90px}
.benefit{width:320px;text-align:center;top:180px}
.benefit svg{display:block;margin:0 auto}
.benefit h3{font-size:19px;font-weight:600;margin-top:20px;text-transform:uppercase}
.benefit p{font-size:17px;line-height:23px;color:var(--muted);margin-top:16px;padding:0 10px}

/* services */
.services{top:1531px;height:652px;background:var(--dark);color:var(--white)}
.services .sec-title{top:42px;font-weight:600}
.card{top:150px;width:302px;height:357px;background:#7f7f7f;border-radius:10px;overflow:hidden}
.card-photo{height:148px;background:linear-gradient(180deg,#1e3a44 0%,#4b5d63 45%,#2c3438 100%)}
.card-body{padding:32px 28px 0}
.card-kicker{font-size:11px;color:#a9a9a9}
.card h4{font-size:13px;font-weight:500;margin-top:8px;text-transform:uppercase}
.card-text{font-size:10.5px;line-height:14px;margin-top:12px;color:#eee}
.explore{top:540px;display:flex;justify-content:center;align-items:center;gap:12px;font-size:22px}

/* join */
.join{top:2183px;height:329px;overflow:hidden}
.join-photo{position:absolute;inset:0;background:radial-gradient(ellipse at 50% 40%,#2a2a2a 0%,#3a3a3a 35%,#6a6a6a 60%,#8a8a8a 100%)}
.cta{left:380px;width:439px;height:80px;background:var(--dark);color:var(--white);font-size:26px;font-weight:500;display:flex;align-items:center;justify-content:center}
.join .cta{top:146px}

/* testimonials */
.testimonials{top:2512px;height:641px;background:var(--white)}
.testimonials .sec-title{top:50px;font-size:32px}
.testimonials .sec-sub{top:92px}
.quote{top:180px;width:316px;height:280px}
.quote-back{position:absolute;left:0;top:14px;width:300px;height:266px;background:#4a4a4a;border-radius:8px}
.quote-card{position:absolute;left:14px;top:0;width:302px;height:266px;background:var(--white);border-radius:8px;box-shadow:0 4px 18px rgba(0,0,0,.12);padding:56px 28px 0}
.stars{display:flex;gap:6px}
.quote-text{font-size:11.5px;line-height:15px;margin-top:28px;color:#333}
.person{display:flex;align-items:center;gap:14px;margin-top:28px}
.avatar{width:44px;height:44px;border-radius:50%;background:linear-gradient(135deg,#8aa4b2,#4f6470)}
.person b{display:block;font-size:12px;font-weight:600}
.person span{font-size:9px;color:#777}
.view-more{top:529px;left:530px;width:139px;height:46px;border:1.5px solid #666;display:flex;align-items:center;justify-content:center;font-size:15px}

/* newsletter */
.newsletter{top:3153px;height:253px;background:var(--dark);color:var(--white)}
.newsletter .sec-title{top:62px;font-size:32px}
.newsletter .sec-sub{top:112px}
.sub-form{left:370px;top:155px;width:456px;height:40px;background:var(--darker);border:1px solid #555;border-radius:4px;display:flex;align-items:center;justify-content:space-between;padding:0 4px 0 18px;font-size:11.5px}
.sub-form span.btn-in{background:#555;border-radius:4px;padding:0 20px;height:32px;display:flex;align-items:center}

/* partners */
.partners{top:3406px;height:127px;background:var(--white)}
.badge-row{left:0;width:1200px;display:flex;justify-content:center;gap:14px}
.badge{height:14px;background:#c9c9c9;border-radius:3px}

/* faq */
.faq{top:3533px;height:437px;background:var(--dark);color:var(--white)}
.faq .sec-title{top:62px;font-size:32px}
.faq-item{left:370px;width:458px;height:44px;border:1px solid #5c5c5c;border-radius:5px;background:var(--darker);display:flex;align-items:center;justify-content:space-between;padding:0 36px 0 18px;font-size:12px}

/* ready */
.ready{top:3970px;height:354px;overflow:hidden}
.ready-photo{position:absolute;inset:0;background:linear-gradient(180deg,#6b6b6b 0%,#a8a8a8 35%,#bdbdbd 55%,#8c8c8c 80%,#4d4d4d 100%)}
.ready .sec-title{top:78px;font-size:32px;color:var(--dark)}
.ready .grey{color:#6f6f6f}
.ready .sec-sub{top:130px;font-size:15px;line-height:20px;color:#333}
.ready .cta{top:197px}

/* footer */
.site-footer{top:4324px;height:334px;background:var(--footer);color:var(--white)}
.brand-lg{left:132px;top:76px;font-size:52px}
.foot-col h5{font-size:17px;font-weight:600;margin-bottom:14px}
.foot-col a{display:block;color:var(--white);text-decoration:none;font-size:12px;height:27px}
.contact-line{display:flex;align-items:center;gap:12px;font-size:12px;height:30px}
.socials{left:132px;top:180px;display:flex;gap:22px;font-size:13px;font-weight:500}
.socials span{display:flex;align-items:center;gap:6px}
.socials i{width:10px;height:10px;border-radius:50%;background:var(--white);display:block}
.rule{top:269px;height:1px;background:#8a8a8a;width:305px}
.copyright{top:258px;font-size:18px}
</style>
</head>
<body>

<header class="hero">
  <div class="hero-photo" role="img" aria-label="Private jet taking off against a grey sky"></div>
  <div class="abs brand brand-sm">Velorane</div>
  <nav class="abs nav"><a href="#">Aircraft</a><a href="#">Programs</a><a href="#">Why Velorane</a><a href="#">Lifestyle</a></nav>
  <h1 class="abs center hero-title">Unlock the Skies:</h1>
  <p class="abs center hero-sub">Your Gateway to Jet Innovation and Luxury</p>
  <div class="abs center hero-actions"><a class="btn btn-solid" href="#">Learn More</a><a class="btn btn-outline" href="#">Contact Us</a></div>
</header>

<section class="intro">
  <div class="abs watermark" aria-hidden="true">Velorane</div>
  <p class="abs">Our Jet Card Program offers a detailed cost structure that ensures financial predictability and exceptional value. With no-long term commitment and guaranteed upgraded subject to availability, It's the ideal program for those who fly 25 hours or fewer per year</p>
  <ul class="abs checks">
    <li><svg width="18" height="18" viewBox="0 0 18 18"><circle cx="9" cy="9" r="9" fill="#fff"/><path d="M5 9.3l2.6 2.6L13 6.5" stroke="#333" stroke-width="2" fill="none"/></svg>Private jet lease programs</li>
    <li><svg width="18" height="18" viewBox="0 0 18 18"><circle cx="9" cy="9" r="9" fill="#fff"/><path d="M5 9.3l2.6 2.6L13 6.5" stroke="#333" stroke-width="2" fill="none"/></svg>All access programs</li>
    <li><svg width="18" height="18" viewBox="0 0 18 18"><circle cx="9" cy="9" r="9" fill="#fff"/><path d="M5 9.3l2.6 2.6L13 6.5" stroke="#333" stroke-width="2" fill="none"/></svg>Helicopter access program</li>
    <li><svg width="18" height="18" viewBox="0 0 18 18"><circle cx="9" cy="9" r="9" fill="#fff"/><path d="M5 9.3l2.6 2.6L13 6.5" stroke="#333" stroke-width="2" fill="none"/></svg>By the seat charter flights</li>
  </ul>
</section>

<section class="benefits">
  <h2 class="abs center sec-title">Benefits of <span class="grey">Choosing us</span></h2>
  <p class="abs center sec-sub">The service we offer for your journey</p>
  <div class="abs benefit" style="left:122px">
    <svg width="88" height="88" viewBox="0 0 88 88"><circle cx="44" cy="44" r="39" fill="none" stroke="#1f1f1f" stroke-width="6"/><path d="M56 31c-2-4-7-6-12-6-7 0-12 4-12 9 0 12 25 6 25 19 0 5-6 9-13 9-6 0-11-3-13-7M44 18v52" fill="none" stroke="#1f1f1f" stroke-width="6" stroke-linecap="round"/></svg>
    <h3>Convenience</h3>
    <p>10 new offers every day. 350 offers on site, trusted by a community of thousands of users.</p>
  </div>
  <div class="abs benefit" style="left:447px">
    <svg width="90" height="88" viewBox="0 0 90 88"><path d="M6 84V26L30 6l24 20v58M54 40h30v44M2 84h86M20 34h20M20 50h20M20 66h20M64 56h10M64 70h10" fill="none" stroke="#1f1f1f" stroke-width="5"/></svg>
    <h3>Luxury</h3>
    <p>Our stress-free finance department that can find financial solutions to save you money.</p>
  </div>
  <div class="abs benefit" style="left:765px">
    <svg width="88" height="88" viewBox="0 0 88 88"><circle cx="44" cy="44" r="39" fill="none" stroke="#1f1f1f" stroke-width="6"/><path d="M56 31c-2-4-7-6-12-6-7 0-12 4-12 9 0 12 25 6 25 19 0 5-6 9-13 9-6 0-11-3-13-7M44 18v52" fill="none" stroke="#1f1f1f" stroke-width="6" stroke-linecap="round"/></svg>
    <h3>Exclusivity</h3>
    <p>Customize your website according to your expectations and requirements</p>
  </div>
</section>

<section class="services">
  <h2 class="abs center sec-title">Service for Your Flight</h2>
  <article class="abs card" style="left:134px">
    <div class="card-photo" role="img" aria-label="Private jet cabin interior with leather seats"></div>
    <div class="card-body"><div class="card-kicker">Your Cabin</div><h4>A Home Away From Home</h4><p class="card-text">Consistent across the whole fleet, welcomes passengers all over the world. Passengers can use a fully enabled business suite or relax in a restful family space. The cabins are equipped for all needs.</p></div>
  </article>
  <article class="abs card" style="left:449px">
    <div class="card-photo" role="img" aria-label="Private jet cabin interior with crew"></div>
    <div class="card-body"><div class="card-kicker">Crew Exellence</div><h4>The Most Experienced Team</h4><p class="card-text">To ensure passengers enjoy unrivaled service as standard, every Velorane flight has at least one Cabin Host as well as two pilots in the flight deck. Pilots only fly one aircraft type, to ensure maximum familiarity and instinctive reactions to any situation, and train twice a year.</p></div>
  </article>
  <article class="abs card" style="left:763px">
    <div class="card-photo" role="img" aria-label="Private jet cabin interior prepared for families"></div>
    <div class="card-body"><div class="card-kicker">Little Explorers</div><h4>Adventures in the Sky</h4><p class="card-text">Velorane offers the most extensive travelers' program for children. Bringing to life extraordinary experiences that combine unique entertainment and educational elements, it is tailored to your child's age and interests to make every journey memorable</p></div>
  </article>
  <div class="abs center explore">Explore more <svg width="28" height="16" viewBox="0 0 28 16"><path d="M1 8h24M18 1l7 7-7 7" fill="none" stroke="#fff" stroke-width="2.2"/></svg></div>
</section>

<section class="join">
  <div class="join-photo" role="img" aria-label="Person in a dark jacket pointing down at the call to action"></div>
  <div class="abs cta">Lets Join Our Program</div>
</section>

<section class="testimonials">
  <h2 class="abs center sec-title">Testimonials</h2>
  <p class="abs center sec-sub">Hear what our client say</p>
  <div class="abs quote" style="left:94px">
    <div class="quote-back"></div>
    <div class="quote-card">
      <div class="stars"><svg width="96" height="14" viewBox="0 0 96 14"><g fill="#f5b301"><path id="s" d="M7 0l2 4.6 5 .4-3.8 3.3 1.2 4.9L7 10.6 2.6 13.2l1.2-4.9L0 5l5-.4z"/><use href="#s" x="20"/><use href="#s" x="40"/><use href="#s" x="60"/></g><use href="#s" x="80" fill="#ddd"/></svg></div>
      <p class="quote-text">Lorem ipsum dolor sit amet consectetur. Eu nunc quis non orci cursus integer sed. A nisl amet enim nec.</p>
      <div class="person"><div class="avatar" role="img" aria-label="Client portrait"></div><div><b>Daniel Ashcroft</b><span>CEO Northwind Ltd</span></div></div>
    </div>
  </div>
  <div class="abs quote" style="left:443px">
    <div class="quote-back"></div>
    <div class="quote-card">
      <div class="stars"><svg width="96" height="14" viewBox="0 0 96 14"><g fill="#f5b301"><use href="#s"/><use href="#s" x="20"/><use href="#s" x="40"/><use href="#s" x="60"/></g><use href="#s" x="80" fill="#ddd"/></svg></div>
      <p class="quote-text">Lorem ipsum dolor sit amet consectetur. Eu nunc quis non orci cursus integer sed. A nisl amet enim nec.</p>
      <div class="person"><div class="avatar" role="img" aria-label="Client portrait"></div><div><b>Daniel Ashcroft</b><span>CEO Northwind Ltd</span></div></div>
    </div>
  </div>
  <div class="abs quote" style="left:793px">
    <div class="quote-back"></div>
    <div class="quote-card">
      <div class="stars"><svg width="96" height="14" viewBox="0 0 96 14"><g fill="#f5b301"><use href="#s"/><use href="#s" x="20"/><use href="#s" x="40"/><use href="#s" x="60"/></g><use href="#s" x="80" fill="#ddd"/></svg></div>
      <p class="quote-text">Lorem ipsum dolor sit amet consectetur. Eu nunc quis non orci cursus integer sed. A nisl amet enim nec.</p>
      <div class="person"><div class="avatar" role="img" aria-label="Client portrait"></div><div><b>Daniel Ashcroft</b><span>CEO Northwind Ltd</span></div></div>
    </div>
  </div>
  <div class="abs view-more">View More</div>
</section>

<section class="newsletter">
  <h2 class="abs center sec-title"><span class="grey" style="color:#5e5e5e">Subscribe</span> Our Newsletter</h2>
  <p class="abs center sec-sub">Get in touch with us</p>
  <div class="abs sub-form"><span>Your e-mail</span><span class="btn-in">Sign up now</span></div>
</section>

<section class="partners">
  <div class="abs badge-row" style="top:37px"><i class="badge" style="width:30px"></i><i class="badge" style="width:62px"></i><i class="badge" style="width:44px"></i><i class="badge" style="width:56px"></i><i class="badge" style="width:66px"></i></div>
  <div class="abs badge-row" style="top:68px"><i class="badge" style="width:46px"></i><i class="badge" style="width:46px"></i><i class="badge" style="width:66px"></i><i class="badge" style="width:66px"></i><i class="badge" style="width:26px"></i><i class="badge" style="width:40px"></i></div>
</section>

<section class="faq">
  <h2 class="abs center sec-title"><span style="color:#5e5e5e">Question?</span> Look here</h2>
  <div class="abs faq-item" style="top:137px"><span>Why us?</span><span>+</span></div>
  <div class="abs faq-item" style="top:202px"><span>How does it work?</span><span>+</span></div>
  <div class="abs faq-item" style="top:267px"><span>How much?</span><span>+</span></div>
  <div class="abs faq-item" style="top:332px"><span>Are the request really unlimited?</span><span>+</span></div>
</section>

<section class="ready">
  <div class="ready-photo" role="img" aria-label="Private jet parked on the tarmac under a cloudy sky"></div>
  <h2 class="abs center sec-title"><span class="grey">Ready to</span> Learn More?</h2>
  <p class="abs center sec-sub">Help you by providing a little information in order to get<br>a lot more information</p>
  <div class="abs cta">Request Info</div>
</section>

<footer class="site-footer">
  <div class="abs brand brand-lg">Velorane</div>
  <div class="abs foot-col" style="left:558px;top:56px"><h5>Menu</h5><a href="#">Aircraft</a><a href="#">Programs</a><a href="#">Why Velorane</a><a href="#">Lifestyle</a></div>
  <div class="abs foot-col" style="left:840px;top:62px"><h5>Contact us</h5>
    <div class="contact-line"><svg width="14" height="14" viewBox="0 0 14 14"><path d="M7 1a4 4 0 014 4c0 3-4 8-4 8S3 8 3 5a4 4 0 014-4z" fill="none" stroke="#fff" stroke-width="1.3"/><circle cx="7" cy="5" r="1.4" fill="#fff"/></svg>218 Harbor Crest Ave, Lumen Bay, FL 30412</div>
    <div class="contact-line"><svg width="14" height="14" viewBox="0 0 14 14"><path d="M3 1l2.5 3-1.5 1.5c1 2 2.5 3.5 4.5 4.5L10 8.5l3 2.5-1.5 2C6 13 1 8 1 2.5z" fill="none" stroke="#fff" stroke-width="1.2"/></svg>(555) 014 2290</div>
    <div class="contact-line"><svg width="14" height="12" viewBox="0 0 14 12"><rect x="1" y="1" width="12" height="10" fill="none" stroke="#fff" stroke-width="1.2"/><path d="M1 1l6 5 6-5" fill="none" stroke="#fff" stroke-width="1.2"/></svg>hello@velorane-mail.com</div>
  </div>
  <div class="abs socials"><span><i></i>Faceline</span><span><i></i>Xpost</span><span><i></i>Pixgram</span><span><i></i>Linkwork</span><span><i></i>Vidtube</span></div>
  <div class="abs rule" style="left:132px"></div>
  <div class="abs center copyright">Copyright © 2024 Velorane</div>
  <div class="abs rule" style="left:763px"></div>
</footer>

</body>
</html>
```